Banner Ad Design Project

Process description of accounting delivery A to Z

Your folder appointment for delivery of receipts, in and outgoing invoices not necessary but possible – goes into a industrial sized scanner at the office

Electronic delivery via email, Nimbus or remote scanning locally at the clients office

Imported into the accounting software (called Ledgerly) with drag and drop from email and Nimbus our directly imported from scanner at clients office

Software sets ledger accounts after scanning largely automated
Imported into accounting softer and finished by producing Income statement , Balance sheet and cash flow statements.

Size should fit the www.brenvalo.no webpage banners rolling

Target Market(s)

New Clients - its to sell our work as modern

Industry/Entity Type

Accounting

Requirements
Must have
• Color scheme fitting current webpage. Looking for a process driven illustration where details are more 1D not 3D as such. Simplified and easy to grasp scheme of flow in our production pipeline.

```html
<!DOCTYPE html>
<html lang="en">
<head>
<meta charset="utf-8">
<title>Brenvalo – Accounting Delivery A-Z</title>
<link href="https://fonts.googleapis.com/css2?family=Questrial&family=Barlow+Semi+Condensed:wght@300&display=swap" rel="stylesheet">
<style>
  :root{
    --green:#1f8a66;
    --green-dark:#17724f;
    --panel:#ececec;
    --side:#d8d8d8;
    --page:#ebebeb;
    --white:#ffffff;
    --ink:#3a3a3a;
    --ink-soft:#555555;
    --rule:#cfcfcf;
  }
  *{box-sizing:border-box;margin:0;padding:0}
  html,body{width:1200px;height:1000px;overflow:hidden;background:var(--white)}
  body{position:relative;font-family:"Questrial",sans-serif;color:var(--ink)}

  .banner-bg{position:absolute;background:var(--panel)}
  .flow{position:absolute;width:768px;height:240px}
  .flow .title{position:absolute;left:165px;top:18px;font-size:18px;font-weight:700;color:var(--ink);letter-spacing:.2px}
  .step{position:absolute}
  .step h3{font-size:14px;font-weight:400;color:var(--ink);white-space:nowrap;line-height:16px}
  .step p{font-size:10px;color:var(--ink-soft);line-height:11px;margin-top:0}
  .step.wrap p{width:232px}
  .arrow{position:absolute;width:18px;height:18px}
  .divider{position:absolute;left:0;right:0;top:150px;height:1px;background:var(--rule)}
  .icon{position:absolute}
  .cloud-name{position:absolute;font-size:17px;line-height:20px;color:var(--ink);display:flex;align-items:center;gap:5px;white-space:nowrap}
  .cloud-name::before{content:"";width:10px;height:10px;border-radius:50%;background:var(--ink)}
  .software-name{position:absolute;font-size:19px;font-weight:700;color:var(--green);display:flex;align-items:center;gap:6px;white-space:nowrap}
  .software-name::before{content:"";width:14px;height:14px;background:var(--green)}

  /* website context */
  .site{position:absolute;left:94px;top:442px;width:1005px;height:516px;background:var(--page)}
  .site .side{position:absolute;top:0;height:295px;background:var(--side)}
  .site .side.left{left:0;width:121px}
  .site .side.right{right:0;width:116px}
  .site .content{position:absolute;left:121px;top:0;width:768px;height:508px;background:var(--white)}
  .navbar{position:absolute;left:231px;top:468px;width:736px;height:26px;background:var(--green)}
  .nav{position:absolute;left:405px;top:475px;display:flex;gap:11px;font-size:10px;color:var(--white);white-space:nowrap}
  .nav .current{font-weight:700}
  .lang{position:absolute;left:924px;top:477px;display:flex;gap:2px}
  .lang span{width:13px;height:8px;background:#e9e9e9;border:1px solid #bbb}
  .brand{position:absolute;left:260px;top:455px;width:101px;height:99px;background:var(--green);border:2px solid var(--white)}
  .brand .name{position:absolute;left:0;right:0;top:64px;text-align:center;font-size:17px;color:var(--white)}
  .tagline{position:absolute;left:256px;top:792px;font-family:"Barlow Semi Condensed",sans-serif;font-weight:300;font-size:30px;line-height:34px;letter-spacing:.6px;color:var(--green);white-space:nowrap}
  .badge{position:absolute;background:#e3e3e3;border:1px solid #b9b9b9}
</style>
</head>
<body>

<!-- standalone banner -->
<div class="banner-bg" style="left:216px;top:80px;width:768px;height:240px"></div>
<section class="flow" style="left:216px;top:80px" aria-label="Accounting delivery process">
  <h2 class="title">Accountind Delivery A-Z</h2>

  <div class="step" style="left:32px;top:70px"><h3>Scan incoming/outgoing receipts</h3><p>and prepare them for delivery</p></div>
  <svg class="arrow" style="left:255px;top:70px" viewBox="0 0 18 18"><circle cx="9" cy="9" r="8" fill="none" stroke="var(--green)" stroke-width="2"/><path d="M4.5 9h8M9 5l4 4-4 4" fill="none" stroke="var(--green)" stroke-width="2"/></svg>
  <div class="step" style="left:286px;top:70px"><h3>Client receives them electronically</h3><p>via email, Nimbus or remote scanning</p></div>
  <svg class="arrow" style="left:516px;top:70px" viewBox="0 0 18 18"><circle cx="9" cy="9" r="8" fill="none" stroke="var(--green)" stroke-width="2"/><path d="M4.5 9h8M9 5l4 4-4 4" fill="none" stroke="var(--green)" stroke-width="2"/></svg>
  <div class="step" style="left:547px;top:70px"><h3>Import to accounting software</h3><p>directly from scanner or by drag and drop</p></div>

  <svg class="icon" style="left:72px;top:103px" width="40" height="36" viewBox="0 0 40 36"><path d="M4 22 L30 2 L36 6 L12 24 Z" fill="none" stroke="var(--ink)" stroke-width="2.5"/><rect x="2" y="24" width="30" height="8" rx="1" fill="var(--ink)"/></svg>
  <svg class="icon" style="left:117px;top:113px" width="10" height="10" viewBox="0 0 10 10"><path d="M5 1v8M1 5h8" stroke="var(--ink)" stroke-width="2"/></svg>
  <svg class="icon" style="left:136px;top:102px" width="30" height="36" viewBox="0 0 30 36"><path d="M2 2h26v32H2z" fill="none" stroke="var(--green)" stroke-width="2" stroke-dasharray="3 2"/><path d="M7 8v20" stroke="var(--green)" stroke-width="2" stroke-dasharray="2 2"/><text x="18" y="30" font-size="9" font-family="Questrial,sans-serif" fill="var(--ink)">$</text></svg>
  <svg class="icon" style="left:171px;top:112px" width="20" height="16" viewBox="0 0 20 16"><path d="M2 4l4-3 4 3M10 8l4 3 4-3" fill="none" stroke="var(--green)" stroke-width="2.5"/></svg>

  <svg class="icon" style="left:290px;top:106px" width="40" height="28" viewBox="0 0 40 28"><rect x="2" y="2" width="36" height="24" fill="none" stroke="var(--green)" stroke-width="2.5"/><path d="M2 2l18 14L38 2" fill="none" stroke="var(--green)" stroke-width="2.5"/></svg>
  <div class="cloud-name" style="left:344px;top:108px">Nimbus</div>
  <svg class="icon" style="left:446px;top:102px" width="48" height="32" viewBox="0 0 48 32"><rect x="2" y="3" width="32" height="21" fill="none" stroke="var(--green)" stroke-width="2.5"/><path d="M12 30h12M18 24v6" stroke="var(--green)" stroke-width="2.5"/><path d="M11 12a10 10 0 0 1 14 0M14 15a6 6 0 0 1 8 0" fill="none" stroke="var(--green)" stroke-width="2"/><circle cx="18" cy="18" r="1.6" fill="var(--green)"/><rect x="38" y="1" width="9" height="29" rx="1" fill="var(--green)"/></svg>
  <div class="software-name" style="left:598px;top:104px">Ledgerly</div>

  <div class="divider"></div>

  <div class="step" style="left:32px;top:158px"><h3>The software creates ledger</h3><p>for each account</p></div>
  <svg class="arrow" style="left:255px;top:158px" viewBox="0 0 18 18"><circle cx="9" cy="9" r="8" fill="none" stroke="var(--green)" stroke-width="2"/><path d="M4.5 9h8M9 5l4 4-4 4" fill="none" stroke="var(--green)" stroke-width="2"/></svg>
  <div class="step wrap" style="left:286px;top:158px"><h3>Generate reports</h3><p>Balance sheet, Income statement and Cash flow statements</p></div>

  <svg class="icon" style="left:74px;top:192px" width="32" height="36" viewBox="0 0 32 36"><path d="M2 6v28h22M5 4v27h22M8 2h20v26H8z" fill="none" stroke="var(--ink)" stroke-width="1.6"/><path d="M12 8h12M12 12h12M12 16h12M12 20h8" stroke="var(--ink)" stroke-width="1.6"/></svg>
  <svg class="icon" style="left:114px;top:203px" width="16" height="14" viewBox="0 0 16 14"><path d="M2 2l5 5-5 5M9 2l5 5-5 5" fill="none" stroke="var(--green)" stroke-width="2.5"/></svg>
  <svg class="icon" style="left:138px;top:192px" width="32" height="36" viewBox="0 0 32 36"><path d="M2 2h18l8 8v24H2z" fill="none" stroke="var(--green)" stroke-width="2"/><path d="M6 10h12M6 14h8M6 18h12" stroke="var(--green)" stroke-width="2"/><circle cx="23" cy="29" r="4" fill="none" stroke="var(--green)" stroke-width="1.6"/></svg>

  <svg class="icon" style="left:367px;top:192px" width="30" height="37" viewBox="0 0 30 37"><rect x="2" y="2" width="26" height="33" fill="none" stroke="var(--ink)" stroke-width="1.8"/><rect x="6" y="6" width="8" height="7" fill="none" stroke="var(--ink)" stroke-width="1.5"/><path d="M17 7h7M17 11h7M6 17h18M6 21h18M6 25h18M6 29h18" stroke="var(--ink)" stroke-width="1.8"/></svg>
  <svg class="icon" style="left:409px;top:192px" width="26" height="37" viewBox="0 0 26 37"><path d="M2 2h16l6 6v27H2z" fill="none" stroke="var(--green)" stroke-width="2"/><path d="M6 12h6M6 18h6M6 24h6M6 30h6M15 12h5M15 18h5M15 24h5M15 30h5" stroke="var(--green)" stroke-width="1.6" stroke-dasharray="2 1"/></svg>
  <svg class="icon" style="left:447px;top:192px" width="30" height="37" viewBox="0 0 30 37"><rect x="2" y="2" width="26" height="33" fill="none" stroke="var(--ink)" stroke-width="1.8"/><path d="M6 7h8M6 11h8M6 17h18M6 21h18M6 25h18M6 29h18" stroke="var(--ink)" stroke-width="1.8"/><text x="18" y="14" font-size="10" font-family="Questrial,sans-serif" fill="var(--ink)">$</text></svg>
</section>

<!-- banner shown on the website -->
<div class="site">
  <div class="side left"></div>
  <div class="side right"></div>
  <div class="content"></div>
</div>
<div class="banner-bg" style="left:231px;top:494px;width:736px;height:243px"></div>
<div class="navbar"></div>
<nav class="nav"><span class="current">Home</span><span>About Brenvalo</span><span>Accountant?</span><span>Services</span><span>Help &amp; Support</span></nav>
<div class="lang"><span></span><span></span></div>
<div class="brand"><div class="name">brenvalo</div></div>

<section class="flow" style="left:216px;top:498px" aria-label="Accounting delivery process">
  <h2 class="title">Accountind Delivery A-Z</h2>

  <div class="step" style="left:32px;top:70px"><h3>Scan incoming/outgoing receipts</h3><p>and prepare them for delivery</p></div>
  <svg class="arrow" style="left:255px;top:70px" viewBox="0 0 18 18"><circle cx="9" cy="9" r="8" fill="none" stroke="var(--green)" stroke-width="2"/><path d="M4.5 9h8M9 5l4 4-4 4" fill="none" stroke="var(--green)" stroke-width="2"/></svg>
  <div class="step" style="left:286px;top:70px"><h3>Client receives them electronically</h3><p>via email, Nimbus or remote scanning</p></div>
  <svg class="arrow" style="left:516px;top:70px" viewBox="0 0 18 18"><circle cx="9" cy="9" r="8" fill="none" stroke="var(--green)" stroke-width="2"/><path d="M4.5 9h8M9 5l4 4-4 4" fill="none" stroke="var(--green)" stroke-width="2"/></svg>
  <div class="step" style="left:547px;top:70px"><h3>Import to accounting software</h3><p>directly from scanner or by drag and drop</p></div>

  <svg class="icon" style="left:72px;top:103px" width="40" height="36" viewBox="0 0 40 36"><path d="M4 22 L30 2 L36 6 L12 24 Z" fill="none" stroke="var(--ink)" stroke-width="2.5"/><rect x="2" y="24" width="30" height="8" rx="1" fill="var(--ink)"/></svg>
  <svg class="icon" style="left:117px;top:113px" width="10" height="10" viewBox="0 0 10 10"><path d="M5 1v8M1 5h8" stroke="var(--ink)" stroke-width="2"/></svg>
  <svg class="icon" style="left:136px;top:102px" width="30" height="36" viewBox="0 0 30 36"><path d="M2 2h26v32H2z" fill="none" stroke="var(--green)" stroke-width="2" stroke-dasharray="3 2"/><path d="M7 8v20" stroke="var(--green)" stroke-width="2" stroke-dasharray="2 2"/><text x="18" y="30" font-size="9" font-family="Questrial,sans-serif" fill="var(--ink)">$</text></svg>
  <svg class="icon" style="left:171px;top:112px" width="20" height="16" viewBox="0 0 20 16"><path d="M2 4l4-3 4 3M10 8l4 3 4-3" fill="none" stroke="var(--green)" stroke-width="2.5"/></svg>

  <svg class="icon" style="left:290px;top:106px" width="40" height="28" viewBox="0 0 40 28"><rect x="2" y="2" width="36" height="24" fill="none" stroke="var(--green)" stroke-width="2.5"/><path d="M2 2l18 14L38 2" fill="none" stroke="var(--green)" stroke-width="2.5"/></svg>
  <div class="cloud-name" style="left:344px;top:108px">Nimbus</div>
  <svg class="icon" style="left:446px;top:102px" width="48" height="32" viewBox="0 0 48 32"><rect x="2" y="3" width="32" height="21" fill="none" stroke="var(--green)" stroke-width="2.5"/><path d="M12 30h12M18 24v6" stroke="var(--green)" stroke-width="2.5"/><path d="M11 12a10 10 0 0 1 14 0M14 15a6 6 0 0 1 8 0" fill="none" stroke="var(--green)" stroke-width="2"/><circle cx="18" cy="18" r="1.6" fill="var(--green)"/><rect x="38" y="1" width="9" height="29" rx="1" fill="var(--green)"/></svg>
  <div class="software-name" style="left:598px;top:104px">Ledgerly</div>

  <div class="divider" style="left:15px;right:17px"></div>

  <div class="step" style="left:32px;top:158px"><h3>The software creates ledger</h3><p>for each account</p></div>
  <svg class="arrow" style="left:255px;top:158px" viewBox="0 0 18 18"><circle cx="9" cy="9" r="8" fill="none" stroke="var(--green)" stroke-width="2"/><path d="M4.5 9h8M9 5l4 4-4 4" fill="none" stroke="var(--green)" stroke-width="2"/></svg>
  <div class="step wrap" style="left:286px;top:158px"><h3>Generate reports</h3><p>Balance sheet, Income statement and Cash flow statements</p></div>

  <svg class="icon" style="left:74px;top:192px" width="32" height="36" viewBox="0 0 32 36"><path d="M2 6v28h22M5 4v27h22M8 2h20v26H8z" fill="none" stroke="var(--ink)" stroke-width="1.6"/><path d="M12 8h12M12 12h12M12 16h12M12 20h8" stroke="var(--ink)" stroke-width="1.6"/></svg>
  <svg class="icon" style="left:114px;top:203px" width="16" height="14" viewBox="0 0 16 14"><path d="M2 2l5 5-5 5M9 2l5 5-5 5" fill="none" stroke="var(--green)" stroke-width="2.5"/></svg>
  <svg class="icon" style="left:138px;top:192px" width="32" height="36" viewBox="0 0 32 36"><path d="M2 2h18l8 8v24H2z" fill="none" stroke="var(--green)" stroke-width="2"/><path d="M6 10h12M6 14h8M6 18h12" stroke="var(--green)" stroke-width="2"/><circle cx="23" cy="29" r="4" fill="none" stroke="var(--green)" stroke-width="1.6"/></svg>

  <svg class="icon" style="left:367px;top:192px" width="30" height="37" viewBox="0 0 30 37"><rect x="2" y="2" width="26" height="33" fill="none" stroke="var(--ink)" stroke-width="1.8"/><rect x="6" y="6" width="8" height="7" fill="none" stroke="var(--ink)" stroke-width="1.5"/><path d="M17 7h7M17 11h7M6 17h18M6 21h18M6 25h18M6 29h18" stroke="var(--ink)" stroke-width="1.8"/></svg>
  <svg class="icon" style="left:409px;top:192px" width="26" height="37" viewBox="0 0 26 37"><path d="M2 2h16l6 6v27H2z" fill="none" stroke="var(--green)" stroke-width="2"/><path d="M6 12h6M6 18h6M6 24h6M6 30h6M15 12h5M15 18h5M15 24h5M15 30h5" stroke="var(--green)" stroke-width="1.6" stroke-dasharray="2 1"/></svg>
  <svg class="icon" style="left:447px;top:192px" width="30" height="37" viewBox="0 0 30 37"><rect x="2" y="2" width="26" height="33" fill="none" stroke="var(--ink)" stroke-width="1.8"/><path d="M6 7h8M6 11h8M6 17h18M6 21h18M6 25h18M6 29h18" stroke="var(--ink)" stroke-width="1.8"/><text x="18" y="14" font-size="10" font-family="Questrial,sans-serif" fill="var(--ink)">$</text></svg>
</section>

<p class="tagline">When you need an expert<br>with good business acumen<br>and local roots...</p>
<div class="badge" style="left:811px;top:805px;width:52px;height:18px" role="img" aria-label="Professional association membership badge"></div>
<div class="badge" style="left:876px;top:796px;width:60px;height:29px" role="img" aria-label="Financial supervisory authority registration badge"></div>

</body>
</html>
```